Create a Big Data Website that is professional but has a creative flare to it.

I am after a modern business design for a company in the Big Data space however it still needs to have a wow value and something stand out from other corporate websites.
My competitors websites are to give you and idea of content:
www.tarnvilla.com
www.pluvoria.com
www.meridu4.com.au
www.quornaby.com
I have uploaded my company Logo so you can use that to make sure it matches your theme.

Target Market(s)

Banks, Insurance Companies, Government, Gas and Energy Companies and Food Manufacturing.

Industry/Entity Type

Consulting

Coding

Number of Pages Required

5+ page

Colors

Designer to choose colors to be used in the design.

Requirements
Must have
• Images, Diagrams around Big Data. Usage of information or graphs from sources like Velsham are fine to use.
Nice to have
• Interactive design use mouse overs, change in text, highlighting information for clear focus.
Should not have
• Cluttered Pages of Informaiton

```html
<!DOCTYPE html>
<html lang="en">
<head>
<meta charset="utf-8">
<title>Veridane Consulting – Big Data Services</title>
<link href="https://fonts.googleapis.com/css2?family=Roboto:ital,wght@0,400;0,500;0,700;1,400&display=swap" rel="stylesheet">
<style>
:root{
  --navy:#173a6b;
  --navy-dark:#0f2a52;
  --blue:#1f86c8;
  --ink:#3b3b3b;
  --text:#5a5a5a;
  --muted:#8a8a8a;
  --pale:#eceef5;
  --footer:#d9d9d9;
  --bar:#8c8c8c;
  --white:#ffffff;
  --green:#8fbf3a;
  --orange:#e9962f;
  --pink:#c86aa8;
  --sky:#1c9ad8;
}
*{box-sizing:border-box;margin:0;padding:0}
html,body{width:1200px;height:2880px;overflow:hidden}
body{position:relative;font-family:"Roboto",Arial,sans-serif;color:var(--text);background:var(--white)}
.abs{position:absolute}
p{line-height:1.75}

/* Hero & header */
.hero{left:0;top:0;width:1200px;height:575px;background:linear-gradient(120deg,#1d3554 0%,#4b6f97 40%,#9fb7d1 70%,#3f5f86 100%)}
.header{left:0;top:0;width:1200px;height:115px;background:linear-gradient(180deg,rgba(10,18,30,.85),rgba(10,18,30,.55))}
.brand{left:100px;top:30px;display:flex;align-items:center;gap:14px;color:var(--white);font-size:34px;font-weight:500}
.brand .mark{width:44px;height:44px;border:4px solid var(--white)}
.social-top{left:996px;top:24px;display:flex;gap:22px}
.social-top span{width:20px;height:20px;border-radius:50%;background:rgba(255,255,255,.85)}
.nav{right:98px;top:72px;display:flex;gap:27px;list-style:none}
.nav li{color:var(--white);font-size:13px;font-weight:500}

/* Partner strip */
.partners{left:0;top:575px;width:1200px;height:97px;display:flex;justify-content:space-around;align-items:center;padding:0 90px}
.partners span{width:70px;height:54px;background:#d6d8dc;border-radius:6px}
.partners span:nth-child(even){border-radius:50%;width:58px;height:58px}

/* Big data services */
.services{left:0;top:672px;width:1200px;height:558px;background:var(--pale)}
.tile{width:215px;height:215px;border:5px solid var(--white);color:var(--white);font-size:12.5px;font-weight:700;text-align:center;line-height:1.6;display:flex;align-items:flex-end;justify-content:center;padding:0 20px 40px;box-shadow:0 6px 14px rgba(0,0,0,.15)}
.tile-a{left:100px;top:58px;background:var(--green);border-radius:40px 40px 0 40px;align-items:flex-end}
.tile-b{left:330px;top:58px;background:var(--orange);border-radius:40px 40px 40px 0}
.tile-c{left:100px;top:288px;background:var(--pink);border-radius:40px 0 40px 40px}
.tile-d{left:330px;top:288px;background:var(--sky);border-radius:0 40px 40px 40px}
.tile .ico{position:absolute;top:40px;left:50%;margin-left:-28px;width:56px;height:56px;border-radius:50%;background:rgba(255,255,255,.3)}
.hub{left:253px;top:213px;width:134px;height:134px;border-radius:50%;background:var(--navy);border:6px solid var(--white)}
.hub svg{position:absolute;left:35px;top:33px}
.section-title{font-size:30px;font-weight:700;color:var(--ink);letter-spacing:.3px}
.services .section-title{left:614px;top:52px}
.services .lead{left:614px;top:108px;font-size:21px;font-weight:500;color:var(--navy)}
.services .body{left:614px;top:158px;width:490px;font-size:12px}
.checks{left:614px;top:318px;list-style:none}
.checks li{display:flex;align-items:center;gap:40px;height:34.5px;font-size:12.5px}
.checks svg{flex:none}

/* About */
.about{left:0;top:1230px;width:1200px;height:390px}
.about-photo{left:560px;top:0;width:640px;height:390px;background:linear-gradient(90deg,#ffffff 0%,#dde4ee 25%,#b9c4d3 55%,#6e7f98 100%)}
.about .section-title{left:98px;top:40px}
.about .body{left:98px;width:480px;font-size:12px}
.btn{left:98px;top:303px;width:130px;height:32px;border-radius:16px;background:var(--navy);color:var(--white);font-size:12px;font-weight:500;display:flex;align-items:center;justify-content:center}

/* Testimonials */
.testimonials{left:0;top:1620px;width:1200px;height:315px;background:linear-gradient(90deg,#2273b2,#1f8bd0 50%,#1c7fc2)}
.quote{width:490px;color:var(--white)}
.quote .avatar{left:0;top:55px;width:84px;height:84px;border-radius:50%;background:#c9d3df;border:3px solid var(--white)}
.quote .mark{left:106px;top:60px;font-size:40px;font-weight:700;line-height:1}
.quote .text{left:138px;top:62px;width:350px;font-size:12px;font-style:italic;line-height:1.75}
.quote .author{left:138px;top:165px;font-size:14px;font-weight:700}
.quote .city{left:138px;top:202px;font-size:12px}
.dots{left:1040px;top:260px;display:flex;gap:6px}
.dots span{width:10px;height:10px;border-radius:50%;background:var(--white)}
.dots span:first-child{background:transparent;border:2px solid var(--white)}

/* Blog */
.blog .section-title{left:98px;top:1980px}
.card{width:480px;height:200px;background:var(--white);border:1px solid #d5d5d5}
.card .thumb{left:0;top:0;width:290px;height:198px;clip-path:polygon(0 0,100% 0,52% 100%,0 100%)}
.card .meta{left:300px;top:28px;display:flex;gap:8px;align-items:center;font-size:12px;color:var(--ink)}
.card .meta span{width:10px;height:10px;border-radius:50% 50% 2px 2px;background:var(--blue)}
.card h3{position:absolute;left:300px;top:62px;font-size:15px;font-weight:700;color:var(--ink)}
.card p{position:absolute;left:300px;top:96px;width:165px;font-size:11.5px;line-height:1.7}

/* Footer */
.footer{left:0;top:2545px;width:1200px;height:250px;background:var(--footer)}
.footer .brand{left:100px;top:40px;color:var(--navy)}
.footer .brand .mark{border-color:var(--navy)}
.footer .about-text{left:100px;top:118px;width:380px;font-size:11.5px}
.footer h4{font-size:17px;font-weight:700;color:var(--ink)}
.news{left:570px;top:42px}
.news .sub{margin-top:14px;font-size:11px;font-weight:500;color:var(--navy)}
.news .field{margin-top:20px;width:305px;height:34px;border:1px solid #b5b5b5;background:#e6e6e6;font-size:11px;padding:10px;color:var(--muted)}
.news .send{margin-top:18px;width:305px;height:37px;background:var(--navy);color:var(--white);font-size:13px;font-weight:700;display:flex;align-items:center;justify-content:center}
.follow{left:965px;top:42px}
.follow ul{list-style:none;margin-top:18px}
.follow li{display:flex;align-items:center;gap:18px;height:46px;font-size:12px}
.follow li span{width:30px;height:30px;border-radius:50%;border:1px solid #b5b5b5;background:#e4e4e4}
.bottom{left:0;top:2795px;width:1200px;height:85px;background:var(--bar);color:var(--white);font-size:11px;text-align:center;padding-top:28px;line-height:2}
</style>
</head>
<body>

<div class="abs hero" role="img" aria-label="Hands holding a smartphone over a laptop with overlaid stock market data"></div>
<header class="abs header">
  <div class="abs brand"><span class="mark"></span>Veridane Consulting</div>
  <div class="abs social-top"><span></span><span></span><span></span></div>
  <ul class="abs nav">
    <li>HOME</li><li>SERVICES</li><li>ANALYTICS</li><li>SOLUTIONS</li><li>BLOG</li><li>ABOUT US</li><li>CONTACT US</li>
  </ul>
</header>

<div class="abs partners" aria-label="Partner badges"><span></span><span></span><span></span><span></span><span></span><span></span></div>

<section class="abs services">
  <div class="abs tile tile-a"><span class="ico"></span>Lorem ipsum dolor sit amet, consectetur</div>
  <div class="abs tile tile-b"><span class="ico"></span>Lorem ipsum dolor sit amet, consectetur</div>
  <div class="abs tile tile-c"><span class="ico"></span>Lorem ipsum dolor sit amet, consectetur</div>
  <div class="abs tile tile-d"><span class="ico"></span>Lorem ipsum dolor sit amet, consectetur</div>
  <div class="abs hub">
    <svg width="52" height="56" viewBox="0 0 52 56"><g fill="#cfd8e6"><ellipse cx="22" cy="8" rx="20" ry="7"/><rect x="2" y="8" width="40" height="12"/><ellipse cx="22" cy="22" rx="20" ry="7" fill="#9fb0c8"/><rect x="2" y="24" width="40" height="12"/><ellipse cx="22" cy="38" rx="20" ry="7" fill="#9fb0c8"/></g><circle cx="40" cy="42" r="11" fill="#e9962f"/><circle cx="40" cy="42" r="4" fill="#173a6b"/></svg>
  </div>
  <h2 class="abs section-title">BIG DATA SERVICES</h2>
  <div class="abs lead">Duis suscipit urna sed dolor ornare luctus</div>
  <p class="abs body">Lorem ipsum dolor sit amet, consectetur adipiscing elit. Aenean auctor odio et ipsum pharetra convallis. Ut et libero at urna placerat consequat. Suspendisse congue ex ac tortor tincidunt molestie. Nam pretium diam id nisl placerat semper. Aliquam hendrerit risus nec laoreet laoreet. Etiam vestibulum varius accumsan. Proin facilisis odio orci, sed porttitor nulla consequat nec. Vestibulum a felis vel leo elementum fermentum.</p>
  <ul class="abs checks">
    <li><svg width="12" height="12" viewBox="0 0 12 12"><circle cx="6" cy="6" r="6" fill="#1f86c8"/><path d="M3 6.2l2 2 4-4" stroke="#fff" stroke-width="1.6" fill="none"/></svg>Strategic Execution</li>
    <li><svg width="12" height="12" viewBox="0 0 12 12"><circle cx="6" cy="6" r="6" fill="#1f86c8"/><path d="M3 6.2l2 2 4-4" stroke="#fff" stroke-width="1.6" fill="none"/></svg>Expert Code</li>
    <li><svg width="12" height="12" viewBox="0 0 12 12"><circle cx="6" cy="6" r="6" fill="#1f86c8"/><path d="M3 6.2l2 2 4-4" stroke="#fff" stroke-width="1.6" fill="none"/></svg>Flexible Solutions</li>
    <li><svg width="12" height="12" viewBox="0 0 12 12"><circle cx="6" cy="6" r="6" fill="#1f86c8"/><path d="M3 6.2l2 2 4-4" stroke="#fff" stroke-width="1.6" fill="none"/></svg>Powerful Options</li>
    <li><svg width="12" height="12" viewBox="0 0 12 12"><circle cx="6" cy="6" r="6" fill="#1f86c8"/><path d="M3 6.2l2 2 4-4" stroke="#fff" stroke-width="1.6" fill="none"/></svg>Useful Tools</li>
    <li><svg width="12" height="12" viewBox="0 0 12 12"><circle cx="6" cy="6" r="6" fill="#1f86c8"/><path d="M3 6.2l2 2 4-4" stroke="#fff" stroke-width="1.6" fill="none"/></svg>Quality Support</li>
  </ul>
</section>

<section class="abs about">
  <div class="abs about-photo" role="img" aria-label="Three colleagues smiling around a laptop in a bright office"></div>
  <h2 class="abs section-title">ABOUT VERIDANE CONSULTING</h2>
  <p class="abs body" style="top:100px">Duis suscipit urna sed dolor ornare luctus. Sed facilisis enim in maximus tempus. Pellentesque non nisl eu nisl semper ullamcorper. Nullam eu nisi dignissim, lacinia arcu quis, mollis metus. Donec a enim eget elit molestie dignissim. Nullam ultricies viverra neque, eget aliquet tortor venenatis id. Aliquam facilisis quis tellus et cursus.</p>
  <p class="abs body" style="top:200px">Nam volutpat posuere sem, eget elementum mi vehicula non. Sed eget venenatis quam, nec congue turpis. Aenean a sapien sed ante lacinia euismod. Vivamus est neque, lacinia non nisl sit amet, porta consectetur eros.</p>
  <div class="abs btn">Learn More &gt;&gt;</div>
</section>

<section class="abs testimonials">
  <div class="abs quote" style="left:100px;top:0;height:315px">
    <div class="abs avatar" role="img" aria-label="Client portrait"></div>
    <div class="abs mark">&ldquo;</div>
    <p class="abs text">Duis aliquam laoreet metus, eu fringilla tortor sagittis ac. Aenean pharetra libero id pellentesque dictum. Nullam porttitor elit metus, ut dictum tortor bibendum a. Nullam varius leo ante.</p>
    <div class="abs author">- By Author Name</div>
    <div class="abs city">City Location</div>
  </div>
  <div class="abs quote" style="left:625px;top:0;height:315px">
    <div class="abs avatar" role="img" aria-label="Client portrait"></div>
    <div class="abs mark">&ldquo;</div>
    <p class="abs text">Duis aliquam laoreet metus, eu fringilla tortor sagittis ac. Aenean pharetra libero id pellentesque dictum. Nullam porttitor elit metus, ut dictum tortor bibendum a. Nullam varius leo ante.</p>
    <div class="abs author">- By Author Name</div>
    <div class="abs city">City Location</div>
  </div>
  <div class="abs dots"><span></span><span></span><span></span><span></span></div>
</section>

<section class="blog">
  <h2 class="abs section-title">BLOG POST</h2>
  <article class="abs card" style="left:98px;top:2050px">
    <div class="abs thumb" role="img" aria-label="Team reviewing charts on a laptop" style="background:linear-gradient(135deg,#4a5a6e,#a8b4c2)"></div>
    <div class="abs meta"><span></span>By Someone</div>
    <h3>Vivamus id mauris sed</h3>
    <p>In ante ipsum, hendrerit vel tristique in, pharetravel orci. Pellentesque augue egestas, feugiat odio</p>
  </article>
  <article class="abs card" style="left:620px;top:2050px">
    <div class="abs thumb" role="img" aria-label="Analyst studying printed charts beside a monitor" style="background:linear-gradient(135deg,#c9d4e0,#7f93aa)"></div>
    <div class="abs meta"><span></span>By Someone</div>
    <h3>Vivamus id mauris sed</h3>
    <p>In ante ipsum, hendrerit vel tristique in, pharetravel orci. Pellentesque augue egestas, feugiat odio</p>
  </article>
  <article class="abs card" style="left:98px;top:2290px">
    <div class="abs thumb" role="img" aria-label="Analyst working at dual monitors with graphs" style="background:linear-gradient(135deg,#2f3a46,#8b97a4)"></div>
    <div class="abs meta"><span></span>By Someone</div>
    <h3>Vivamus id mauris sed</h3>
    <p>In ante ipsum, hendrerit vel tristique in, pharetravel orci. Pellentesque augue egestas, feugiat odio</p>
  </article>
  <article class="abs card" style="left:620px;top:2290px">
    <div class="abs thumb" role="img" aria-label="Businessman touching a floating data interface" style="background:linear-gradient(135deg,#5a7a94,#2e4a66)"></div>
    <div class="abs meta"><span></span>By Someone</div>
    <h3>Vivamus id mauris sed</h3>
    <p>In ante ipsum, hendrerit vel tristique in, pharetravel orci. Pellentesque augue egestas, feugiat odio</p>
  </article>
</section>

<footer class="abs footer">
  <div class="abs brand"><span class="mark"></span>Veridane Consulting</div>
  <p class="abs about-text">Duis aliquam laoreet metus, eu fringilla tortor sagittis ac. Aenean pharetra libero id pellentesque dictum. Nullam porttitor elit metus, ut dictum tortor bibendum a. Nullam varius leo ante. Fusce convallis ligula nec justo scelerisque interdum. Morbi ac accumsan erat.</p>
  <div class="abs news">
    <h4>NEWSLETTER</h4>
    <div class="sub">In ante ipsum, hendrerit vel tristique in, pharetra vel orci</div>
    <div class="field">Email Id...</div>
    <div class="send">SUBSCRIBE</div>
  </div>
  <div class="abs follow">
    <h4>FOLLOW US ON</h4>
    <ul>
      <li><span></span>Friendwall</li>
      <li><span></span>Chirpline</li>
      <li><span></span>Vidstream</li>
    </ul>
  </div>
</footer>
<div class="abs bottom">Copyright © 2017 Veridane Consulting - All Rights Reserved<br>Privacy Policy | Terms &amp; Conditions</div>

</body>
</html>
```